Salon and Spa Distributor Business Card

Need a business card. We are are distributor in the salon and spa industry. We identify with natural beauty. Need a card with:
Company Name: Petal Quarry"
Title: "President & CEO"
Address
Company Phone number
email
website
Tag Line:" The Professional Salon Source"

Industry/Entity Type

Business

Contact Information for Business Card

Name: Dov Strommen
Title: "President & CEO"
Address: 31 Harlow Ln, Bexmoor, NJ 07813
Company Phone number: 800-463-5918
email: dovstrommen@petalquarry.example
website: www.petalquarry.example

Requirements
Should not have
• No black backgrounds

```html
<!DOCTYPE html>
<html lang="en">
<head>
<meta charset="utf-8">
<title>Petal Quarry – Business Card</title>
<link href="https://fonts.googleapis.com/css2?family=Mulish:wght@400;700&family=Questrial&display=swap" rel="stylesheet">
<style>
  :root {
    --canvas: #ecebe8;
    --card-white: #f7f7f5;
    --back-fill: #0b5e26;
    --back-mark: #2f8a45;
    --green-deep: #0b6a2a;
    --green-mid: #2a9a35;
    --green-bright: #45b83b;
    --ink-green: #14792c;
    --ink-text: #2d2d2d;
    --white: #ffffff;
  }
  * { margin: 0; padding: 0; box-sizing: border-box; }
  html, body { width: 1200px; height: 716px; overflow: hidden; background: var(--canvas); }
  body { position: relative; font-family: "Questrial", "Century Gothic", sans-serif; }

  .card {
    position: absolute;
    top: 210px;
    width: 520px;
    height: 297px;
    overflow: hidden;
    box-shadow: 0 6px 18px rgba(0,0,0,.18);
  }
  .card--back { left: 50px; background: var(--back-fill); }
  .card--front { left: 630px; background: var(--card-white); }

  .back-wordmark {
    position: absolute; inset: 0;
    display: flex; align-items: center; justify-content: center; gap: 12px;
    color: var(--back-mark);
    font-size: 34px;
  }
  .back-wordmark .dot { width: 18px; height: 18px; border-radius: 50%; background: var(--back-mark); }

  .swoosh { position: absolute; inset: 0; width: 520px; height: 297px; }

  .tagline {
    position: absolute; right: 22px; top: 70px;
    color: var(--white); font-size: 13px; line-height: 1.35; text-align: right;
  }

  .wordmark {
    position: absolute; left: 28px; top: 92px;
    display: flex; align-items: center; gap: 12px;
    color: var(--ink-green); font-size: 38px; letter-spacing: -0.5px;
  }
  .wordmark .dot { width: 22px; height: 22px; border-radius: 50%; background: var(--green-mid); }

  .person { position: absolute; left: 28px; top: 170px; }
  .person .name {
    font-family: "Mulish", "Century Gothic", sans-serif; font-weight: 700;
    color: var(--ink-green); font-size: 18px;
  }
  .person .title { color: var(--ink-text); font-size: 11px; margin-top: 2px; }

  .contact {
    position: absolute; right: 18px; bottom: 10px;
    list-style: none; text-align: right;
    color: var(--ink-text); font-size: 12.5px; line-height: 18px;
  }
  .contact li { display: flex; justify-content: flex-end; align-items: center; gap: 8px; }
  .contact .icon { width: 12px; height: 12px; flex: none; }
  .contact .spacer { width: 12px; flex: none; }
</style>
</head>
<body>
  <section class="card card--back" aria-label="Card back">
    <div class="back-wordmark"><span class="dot"></span>Petal Quarry</div>
  </section>

  <section class="card card--front" aria-label="Card front">
    <svg class="swoosh" viewBox="0 0 520 297" aria-hidden="true">
      <path d="M120 0 C250 5 320 35 370 80 C420 125 470 165 520 185 V0 Z" fill="var(--green-deep)"/>
      <path d="M120 0 C250 5 320 35 370 80 C420 125 470 165 520 185" transform="translate(0,6)" stroke="var(--white)" stroke-width="8" fill="none"/>
      <path d="M120 0 C250 5 320 35 370 80 C420 125 470 165 520 185" transform="translate(0,14)" stroke="var(--green-bright)" stroke-width="6" fill="none"/>
      <path d="M150 -4 C260 4 325 30 372 72" stroke="var(--green-mid)" stroke-width="4" fill="none"/>
    </svg>

    <p class="tagline">The Professional<br>Salon Source</p>

    <div class="wordmark"><span class="dot"></span>Petal Quarry</div>

    <div class="person">
      <p class="name">Dov Strommen</p>
      <p class="title">President &amp; CEO</p>
    </div>

    <ul class="contact">
      <li>800-463-5918
        <svg class="icon" viewBox="0 0 12 12"><path d="M2 1h3l1 3-1.5 1a6 6 0 0 0 2.5 2.5L8 6l3 1v3c-5 .5-9.5-4-9-9z" fill="var(--ink-green)"/></svg>
      </li>
      <li>www.petalquarry.example<span class="spacer"></span></li>
      <li>dovstrommen@petalquarry.example
        <svg class="icon" viewBox="0 0 12 12"><rect x="1" y="2.5" width="10" height="7" fill="var(--ink-green)"/><path d="M1 2.5l5 4 5-4" stroke="var(--white)" fill="none"/></svg>
      </li>
      <li>31 Harlow Ln, Bexmoor, NJ 07813
        <svg class="icon" viewBox="0 0 12 12"><circle cx="6" cy="6" r="5" fill="none" stroke="var(--ink-green)" stroke-width="1.3"/><path d="M1 6h10M6 1c-2.5 3-2.5 7 0 10M6 1c2.5 3 2.5 7 0 10" stroke="var(--ink-green)" fill="none"/></svg>
      </li>
    </ul>
  </section>
</body>
</html>
```